Copper Field Agency Website - Wordpress Web UPDATED BRIEF

FINAL LOGO UPLOADED - please look to this as reference for how we would like the site to look and feel.

We are a digital marketing agency - looking to have a new website built. We are looking for a simple one page feel of site that will allow us to grow it later. (Feel free to take some liberties with that if your imagination veers off) Must be very, playful, bold, sleek and easily integrate video. Wordpress only.

Overview:

Copper Field is a creative constellation. We are built on what's great about the shared economy. With access to thousands of content creators, designers, technicians, writers, strategists and other creatives around the world, we are built differently than a traditional “brick and mortar” Marketing Agency. We provide the traditional services our clients have come to expect, without the “5X factor” of covering the overhead common in the old agency model. We believe even better work can be created in collaboration with our clients and by passing those savings back to them for their use. Our clients pay for our art, our work and our passion –not our furniture.

"Copper Field, Let's Build Together"

Target Market(s)

companies looking for creative agency help, video production, creative consulting and coaching

Industry/Entity Type

Digital Marketing

Coding

Coded - Design and coding required

Number of Pages Required

1 page

Font styles to use
Sans Serif

Colors
3277b5
33a6d7
ec1f27

Requirements
Must have
• Wordpress design is a must. Looking for a one sheet homepage - with sections that are all on the main front page. We will have videos to embed, and should be able to have client logos and easy access to show a variety of our creative work.
• Please look to the logo for how we would like the site to feel.
• Please think "icon process flow" instead of blocks of text (which we used to have). Use the text to explain what the process flow should represent - don't actually copy paste the text but show it visually in icons.
Nice to have
• innovation around how we show video content. solid colors complementary to our palette and aesthetic.
Should not have
• Standard HTML coding

```html
<!DOCTYPE html>
<html lang="en">
<head>
<meta charset="utf-8">
<title>Copper Field Agency</title>
<link href="https://fonts.googleapis.com/css2?family=Lato:wght@400;700;900&display=swap" rel="stylesheet">
<style>
:root{
  --blue:#2066ae;
  --navy:#1a5590;
  --sky:#33a6d7;
  --red:#e3061c;
  --ink:#3a3a3a;
  --muted:#555;
  --light:#f4f4f5;
  --orange:#f7873f;
  --slate:#5f8aa8;
  --plum:#4a2652;
  --pink:#e11a5c;
  --dark:#111;
  --client:#4a4a4a;
}
*{box-sizing:border-box;margin:0;padding:0}
html,body{width:1200px;height:4568px;overflow:hidden}
body{position:relative;font-family:'Lato',sans-serif;color:var(--ink);background:#fff}
.abs{position:absolute}
.section-title{position:absolute;left:0;width:1200px;text-align:center;font-weight:700;font-size:28px;color:var(--blue);letter-spacing:.3px}
.section-sub{position:absolute;left:300px;width:600px;text-align:center;font-size:13.5px;line-height:23px;color:var(--muted)}
.btn{position:absolute;display:flex;align-items:center;justify-content:center;font-size:13px;font-weight:700;color:#fff;background:var(--sky);letter-spacing:.4px}

/* header */
.site-header{position:absolute;left:0;top:0;width:1200px;height:85px;background:#fff;z-index:5}
.brand{position:absolute;left:70px;top:30px;font-weight:900;font-size:18px;color:var(--dark);letter-spacing:.5px}
.main-nav{position:absolute;top:40px;left:0;width:1200px;font-size:12px;font-weight:700;color:#222}
.main-nav span{position:absolute;transform:translateX(-50%);white-space:nowrap}
.main-nav .active{color:var(--red)}

/* hero */
.hero{position:absolute;left:0;top:85px;width:1200px;height:615px;background:linear-gradient(100deg,#4a4c52 0%,#6b6a68 40%,#5a5854 70%,#3d3e44 100%)}
.hero-shade{position:absolute;inset:0;background:rgba(20,22,28,.35)}
.hero-title{position:absolute;left:0;top:235px;width:1200px;text-align:center;font-size:88px;font-weight:900;color:#fff;letter-spacing:1px}
.hero-sub{position:absolute;left:0;top:334px;width:1200px;text-align:center;font-size:28px;color:#fff}

/* about */
.about-art{position:absolute;left:110px;top:755px;width:310px;height:345px;border-radius:8px;background:linear-gradient(160deg,#e7eef7 0%,#c9daee 60%,#dfe6ef 100%)}
.about-title{position:absolute;left:525px;top:765px;font-size:28px;font-weight:700;color:var(--blue)}
.about-text{position:absolute;left:525px;top:812px;width:600px;font-size:13.5px;line-height:31.5px;color:var(--muted)}

/* services */
.diamond{position:absolute;width:140px;height:140px;margin:-70px 0 0 -70px;transform:rotate(45deg);border:9px solid;border-radius:26px;background:#fff}
.d-label{position:absolute;width:180px;margin-left:-90px;text-align:center;font-size:18px;font-weight:700;color:#333;line-height:22px}
.d-icon{position:absolute;margin-left:-16px}

/* video */
.video-frame{position:absolute;left:165px;top:1950px;width:872px;height:415px;background:linear-gradient(135deg,#d9dbd9,#eeeeea 50%,#cfd1cc)}
.play{position:absolute;left:563px;top:2119px;width:76px;height:76px;border-radius:50%;background:#fff;box-shadow:0 2px 8px rgba(0,0,0,.2)}

/* works */
.work-card{position:absolute;top:2629px;width:331px;height:226px}
.work-card.feature{background:linear-gradient(135deg,#4c4f55,#2f3136)}
.work-card h3{position:absolute;left:0;top:60px;width:100%;text-align:center;color:#fff;font-size:19px;font-weight:700}
.work-card p{position:absolute;left:28px;top:92px;width:275px;text-align:center;color:#eee;font-size:13.5px;line-height:23px}
.arrow{position:absolute;top:2730px}

/* clients */
.client{position:absolute;transform:translateX(-50%);font-size:24px;font-weight:700;color:var(--client);white-space:nowrap}

/* testimonials */
.testi-art{position:absolute;left:110px;top:3518px;width:325px;height:338px;border-radius:8px;background:linear-gradient(150deg,#eef1f5 0%,#dfe7f1 55%,#eceef2 100%)}
.avatar{position:absolute;left:525px;width:88px;height:88px;border-radius:50%;background:#c9cdd2;border:3px solid #fff;box-shadow:0 0 0 1px #ddd}
.quote{position:absolute;left:642px;width:480px;font-size:13.5px;line-height:24px;color:var(--muted)}
.quote b{display:block;color:var(--red);font-size:13px;font-weight:700}

/* contact */
.contact{position:absolute;left:0;top:3925px;width:1200px;height:580px;background:linear-gradient(160deg,#1d4e98 0%,#1f68bd 50%,#1b59ac 100%)}
.contact-title{position:absolute;left:0;top:4005px;width:1200px;text-align:center;font-size:28px;font-weight:700;color:#fff}
.contact-info{position:absolute;left:0;top:4065px;width:1200px;font-size:13px;color:#fff;display:flex;justify-content:center;align-items:center;gap:10px}
.field{position:absolute;background:#fff;border-radius:3px;font-size:13px;font-weight:700;color:#222;padding:14px 16px}
.submit{position:absolute;left:525px;top:4358px;width:165px;height:41px;background:var(--red);color:#fff;font-weight:700;font-size:13px;display:flex;align-items:center;justify-content:center}

/* footer */
.site-footer{position:absolute;left:0;top:4502px;width:1200px;height:66px;background:var(--dark)}
.foot-brand{position:absolute;left:70px;top:4524px;font-weight:900;font-size:14px;color:#fff}
.copyright{position:absolute;left:200px;top:4526px;font-size:11px;color:#bbb}
.social{position:absolute;top:4524px;left:930px;display:flex;gap:16px;font-size:12px;font-weight:700;color:#fff}
</style>
</head>
<body>

<header class="site-header">
  <div class="brand">COPPER FIELD</div>
  <nav class="main-nav">
    <span class="active" style="left:337px">HOME</span>
    <span style="left:436px">ABOUT US</span>
    <span style="left:546px">SERVICES</span>
    <span style="left:642px">VIDEO</span>
    <span style="left:734px">WORKS</span>
    <span style="left:830px">CLIENTS</span>
    <span style="left:950px">TESTIMONIALS</span>
    <span style="left:1085px">CONTACT US</span>
  </nav>
</header>

<section class="hero" role="img" aria-label="Team of colleagues meeting around a table with laptops">
  <div class="hero-shade"></div>
  <h1 class="hero-title">COPPER FIELD</h1>
  <p class="hero-sub">Lorem ipsum dolor sit amet, consectetur adipiscing elit</p>
</section>
<svg class="abs" style="left:0;top:670px" width="1200" height="32" viewBox="0 0 1200 32">
  <polygon points="0,32 1200,32 1200,0" fill="var(--red)"/>
  <polygon points="0,32 1200,32 1200,22 560,28" fill="#fff"/>
</svg>

<section>
  <div class="about-art" role="img" aria-label="Company mascot artwork"></div>
  <h2 class="about-title">ABOUT OUR COMPANY</h2>
  <p class="about-text">Copper Field is a creative constellation. We are built on what's great about the shared economy. With access to thousands of content creators, designers, technicians, writers, strategists and other creatives around the world, we are built differently than a traditional “brick and mortar” Marketing Agency. We provide the traditional services our clients have come to expect, without the “5X factor” of covering the overhead common in the old agency model.</p>
  <div class="btn" style="left:525px;top:1033px;width:165px;height:41px">READ MORE</div>
</section>

<section>
  <div class="abs" style="left:0;top:1170px;width:1200px;height:617px;background:var(--light)"></div>
  <svg class="abs" style="left:0;top:1168px" width="1200" height="24" viewBox="0 0 1200 24">
    <polygon points="0,0 1200,0 1200,3 600,10 0,24" fill="#fff"/>
    <polygon points="0,0 0,24 600,10 600,6" fill="var(--sky)"/>
  </svg>
  <svg class="abs" style="left:0;top:1762px" width="1200" height="26" viewBox="0 0 1200 26">
    <polygon points="600,26 1200,0 1200,26" fill="var(--red)"/>
    <polygon points="0,26 1200,26 1200,18 600,26" fill="#fff"/>
  </svg>
  <h2 class="section-title" style="top:1245px">OUR SERVICES</h2>
  <p class="section-sub" style="top:1291px">Curabitur vel dapibus mauris. Integer facilisis arcu ut purus auctor pellentesque. Sed sit amet pellentesque lorem,</p>

  <svg class="abs" style="left:0;top:1380px" width="1200" height="320" viewBox="0 1380 1200 320">
    <line x1="172" y1="1471" x2="314" y2="1613" stroke="var(--navy)" stroke-width="26"/>
    <line x1="314" y1="1613" x2="457" y2="1471" stroke="var(--plum)" stroke-width="26"/>
    <line x1="457" y1="1471" x2="599" y2="1613" stroke="var(--orange)" stroke-width="26"/>
    <line x1="599" y1="1613" x2="743" y2="1471" stroke="var(--pink)" stroke-width="26"/>
    <line x1="743" y1="1471" x2="883" y2="1613" stroke="var(--slate)" stroke-width="26"/>
    <line x1="883" y1="1613" x2="1028" y2="1471" stroke="var(--navy)" stroke-width="26"/>
  </svg>

  <div class="diamond" style="left:172px;top:1471px;border-color:var(--navy)"></div>
  <div class="diamond" style="left:457px;top:1471px;border-color:var(--orange)"></div>
  <div class="diamond" style="left:743px;top:1471px;border-color:var(--slate)"></div>
  <div class="diamond" style="left:1028px;top:1471px;border-color:var(--plum)"></div>
  <div class="diamond" style="left:314px;top:1613px;border-color:var(--plum)"></div>
  <div class="diamond" style="left:599px;top:1613px;border-color:var(--pink)"></div>
  <div class="diamond" style="left:883px;top:1613px;border-color:var(--navy)"></div>

  <svg class="d-icon" style="left:172px;top:1428px" width="32" height="32" viewBox="0 0 32 32" fill="none" stroke="var(--navy)" stroke-width="2.4"><circle cx="14" cy="14" r="9"/><circle cx="14" cy="14" r="4"/><line x1="21" y1="21" x2="29" y2="29"/></svg>
  <div class="d-label" style="left:172px;top:1468px">Discovery</div>

  <svg class="d-icon" style="left:457px;top:1428px" width="32" height="32" viewBox="0 0 32 32" fill="none" stroke="var(--orange)" stroke-width="2.4"><rect x="3" y="3" width="26" height="26"/><line x1="9" y1="24" x2="9" y2="14"/><line x1="14" y1="24" x2="14" y2="9"/><line x1="19" y1="24" x2="19" y2="12"/><line x1="24" y1="24" x2="24" y2="16"/></svg>
  <div class="d-label" style="left:457px;top:1468px">Strategy</div>

  <svg class="d-icon" style="left:743px;top:1416px" width="32" height="32" viewBox="0 0 32 32" fill="none" stroke="var(--navy)" stroke-width="2.4"><circle cx="16" cy="16" r="12"/><circle cx="16" cy="16" r="6"/><path d="M16 10 V16 H22"/></svg>
  <div class="d-label" style="left:743px;top:1456px">Project<br>Management</div>

  <svg class="d-icon" style="left:1028px;top:1428px" width="32" height="32" viewBox="0 0 32 32" fill="none" stroke="var(--navy)" stroke-width="2.4"><path d="M7 3 H20 L26 9 V29 H7 Z"/><line x1="11" y1="15" x2="22" y2="15"/><line x1="11" y1="20" x2="22" y2="20"/><line x1="11" y1="25" x2="18" y2="25"/></svg>
  <div class="d-label" style="left:1028px;top:1468px">Content</div>

  <svg class="d-icon" style="left:314px;top:1571px" width="32" height="32" viewBox="0 0 32 32" fill="none" stroke="var(--navy)" stroke-width="2.4"><rect x="3" y="8" width="19" height="16" rx="2"/><path d="M22 14 L29 10 V22 L22 18"/></svg>
  <div class="d-label" style="left:314px;top:1614px">Production</div>

  <svg class="d-icon" style="left:599px;top:1571px" width="32" height="32" viewBox="0 0 32 32" fill="none" stroke="var(--navy)" stroke-width="2.4"><rect x="2" y="8" width="28" height="16" rx="2"/><circle cx="16" cy="16" r="5"/><rect x="6" y="11" width="20" height="10"/></svg>
  <div class="d-label" style="left:599px;top:1614px">Paid Media</div>

  <svg class="d-icon" style="left:883px;top:1571px" width="32" height="32" viewBox="0 0 32 32" fill="none" stroke="var(--navy)" stroke-width="2.4"><rect x="6" y="7" width="20" height="14" rx="1"/><path d="M2 25 H30"/></svg>
  <div class="d-label" style="left:883px;top:1614px">Coaching</div>
</section>

<section>
  <h2 class="section-title" style="top:1832px">WATCH A VIDEO</h2>
  <p class="section-sub" style="top:1878px">Curabitur vel dapibus mauris. Integer facilisis arcu ut purus auctor pellentesque. Sed sit amet pellentesque lorem,</p>
  <div class="video-frame" role="img" aria-label="Video cover: hand-drawn digital marketing plan on grid paper with pencils"></div>
  <svg class="play" viewBox="0 0 76 76"><polygon points="30,22 56,38 30,54" fill="#111"/></svg>
</section>

<section>
  <div class="abs" style="left:0;top:2437px;width:1200px;height:608px;background:var(--light)"></div>
  <svg class="abs" style="left:0;top:2430px" width="1200" height="26" viewBox="0 0 1200 26">
    <polygon points="0,0 1200,0 1200,4 600,10 0,26" fill="#fff"/>
    <polygon points="0,0 0,26 600,10 600,6" fill="var(--sky)"/>
  </svg>
  <h2 class="section-title" style="top:2504px">OUR CREATIVE WORK</h2>
  <p class="section-sub" style="top:2549px">Curabitur vel dapibus mauris. Integer facilisis arcu ut purus auctor pellentesque. Sed sit amet pellentesque lorem,</p>

  <svg class="arrow" style="left:44px" width="18" height="26" viewBox="0 0 18 26"><polyline points="14,3 4,13 14,23" fill="none" stroke="#555" stroke-width="3"/></svg>
  <div class="work-card feature" style="left:74px" role="img" aria-label="Project photo of a creative workspace">
    <h3>PROJECT HEADING</h3>
    <p>Vivamus sit amet elit porta, elementum nisi non, ornare justo viverra posuere justo, ac porta commodo volutpat..</p>
  </div>
  <div class="work-card" style="left:436px;background:linear-gradient(135deg,#3a6ea8,#8fb6dc 50%,#2c4f7a)" role="img" aria-label="Project photo of social apps on laptop and phone screens"></div>
  <div class="work-card" style="left:798px;background:linear-gradient(135deg,#d8dde3,#7fa6d2 45%,#2b5a9b)" role="img" aria-label="Project photo of a tablet showing 3D business charts"></div>
  <svg class="arrow" style="left:1138px" width="18" height="26" viewBox="0 0 18 26"><polyline points="4,3 14,13 4,23" fill="none" stroke="#555" stroke-width="3"/></svg>

  <div class="btn" style="left:525px;top:2916px;width:165px;height:44px">VIEW ALL WORKS</div>
</section>

<section>
  <svg class="abs" style="left:0;top:3020px" width="1200" height="26" viewBox="0 0 1200 26">
    <polygon points="600,26 1200,0 1200,26" fill="var(--red)"/>
    <polygon points="0,26 1200,26 1200,20 600,26" fill="#fff"/>
  </svg>
  <h2 class="section-title" style="top:3089px">OUR CLIENTS</h2>
  <div class="client" style="left:253px;top:3184px">Harbor Super</div>
  <div class="client" style="left:532px;top:3184px">Civic Law Guild</div>
  <div class="client" style="left:739px;top:3184px">Quarrix</div>
  <div class="client" style="left:1005px;top:3184px">Kinsley Care</div>
  <div class="client" style="left:204px;top:3290px">Vela Health</div>
  <div class="client" style="left:470px;top:3290px">Northbank</div>
  <div class="client" style="left:735px;top:3290px">lotsmarket</div>
  <div class="client" style="left:1014px;top:3290px">AppGrove</div>
</section>

<section>
  <div class="abs" style="left:0;top:3400px;width:1200px;height:525px;background:var(--light)"></div>
  <svg class="abs" style="left:0;top:3382px" width="1200" height="24" viewBox="0 0 1200 24">
    <polygon points="0,0 1200,0 1200,24 0,24" fill="var(--light)"/>
    <polygon points="0,0 1200,0 1200,6 600,10 0,22" fill="#fff"/>
    <polygon points="0,0 0,22 600,10 600,7" fill="var(--sky)"/>
  </svg>
  <h2 class="section-title" style="top:3457px">TESTIMONIALS</h2>
  <div class="testi-art" role="img" aria-label="Isometric illustration of data analysis with charts and a magnifier"></div>

  <div class="avatar" style="top:3563px" role="img" aria-label="Client portrait"></div>
  <p class="quote" style="top:3555px">“ Curabitur vel dapibus mauris. Integer facilisis arcu ut purus auctor pellentesque. Sed sit amet pellentesque loreme tiam lectus libero, hendrerit quis libero et, accumsan imperdiet augue...”<b>-NAME HEADING</b></p>
  <div class="abs" style="left:523px;top:3678px;width:604px;height:1px;background:#ddd"></div>
  <div class="avatar" style="top:3705px" role="img" aria-label="Client portrait"></div>
  <p class="quote" style="top:3697px">“ Curabitur vel dapibus mauris. Integer facilisis arcu ut purus auctor pellentesque. Sed sit amet pellentesque loreme tiam lectus libero, hendrerit quis libero et, accumsan imperdiet augue...”<b>-NAME HEADING</b></p>
</section>

<section>
  <div class="contact" role="img" aria-label="Blue-toned photo of a person working at a laptop"></div>
  <svg class="abs" style="left:0;top:3912px" width="1200" height="26" viewBox="0 0 1200 26">
    <polygon points="0,14 600,13 1200,0 1200,26 0,26" fill="var(--red)"/>
    <polygon points="0,16 1200,10 1200,26 0,26" fill="#1d4e98"/>
  </svg>
  <h2 class="contact-title">CONTACT US</h2>
  <div class="contact-info">
    <svg width="10" height="13" viewBox="0 0 10 13"><path d="M5 0a5 5 0 0 0-5 5c0 4 5 8 5 8s5-4 5-8a5 5 0 0 0-5-5z" fill="#fff"/><circle cx="5" cy="5" r="2" fill="#1f62b5"/></svg>
    <span>14 Alder Court, Maple Street, Springfield, USA</span><span>|</span>
    <svg width="12" height="12" viewBox="0 0 12 12"><path d="M2 0l2 3-1 1.5c.8 1.8 2 3 3.5 3.5L8 7l3 2-1 2.5C5 11.5.5 7 .5 2z" fill="#fff"/></svg>
    <span>1-800-555-0142</span><span>|</span>
    <svg width="13" height="10" viewBox="0 0 13 10"><rect width="13" height="10" fill="#fff"/><polyline points="0,0 6.5,5.5 13,0" fill="none" stroke="#1f62b5" stroke-width="1.4"/></svg>
    <span>info@copperfieldagency.com</span>
  </div>
  <div class="field" style="left:253px;top:4124px;width:334px;height:45px">Name</div>
  <div class="field" style="left:615px;top:4124px;width:333px;height:45px">Email Address</div>
  <div class="field" style="left:253px;top:4181px;width:334px;height:45px">Phone No</div>
  <div class="field" style="left:615px;top:4181px;width:333px;height:45px">Subject</div>
  <div class="field" style="left:253px;top:4240px;width:695px;height:87px">Message</div>
  <div class="submit">SUBMIT</div>
</section>

<footer>
  <svg class="abs" style="left:0;top:4480px" width="1200" height="24" viewBox="0 0 1200 24">
    <polygon points="0,24 1200,0 1200,24" fill="var(--dark)"/>
  </svg>
  <div class="site-footer"></div>
  <div class="foot-brand">COPPER FIELD</div>
  <p class="copyright">Copyright © 2019 Company Name All rights reserved.</p>
  <div class="social"><span>Kite</span><span>Lens</span><span>Chirp</span><span>Linkr</span><span>Tubo</span></div>
</footer>

</body>
</html>
```